Haulage company, lets use ruby red white and some 3rd color for web design. and Garvel Pryce Transport logo

Target Market(s)

Transport industry

Industry/Entity Type

transport

Number of Pages Required

2 page

Requirements
Must have
• Logo

```html
<!DOCTYPE html>
<html lang="en">
<head>
<meta charset="utf-8">
<title>Garvel Pryce Transport</title>
<link href="https://fonts.googleapis.com/css2?family=Lato:ital,wght@0,400;0,700;0,900;1,400&display=swap" rel="stylesheet">
<style>
:root{
  --ruby:#8c3f52;
  --navy:#1f3441;
  --ink:#2b2b2b;
  --white:#fff;
  --footer:#111214;
  --star:#f2c21b;
}
*{box-sizing:border-box;margin:0;padding:0}
html,body{width:1200px;height:3558px;overflow:hidden;background:var(--white)}
body{font-family:'Lato',sans-serif;color:var(--ink);position:relative}
/* header */
.site-header{position:absolute;left:0;top:0;width:1200px;height:86px;background:var(--white)}
.brand{position:absolute;left:144px;top:27px;display:flex;align-items:center;gap:10px}
.brand-mark{width:22px;height:22px;background:var(--ruby)}
.brand-name{font-weight:900;font-size:27px;color:var(--navy);line-height:32px;white-space:nowrap}
.main-nav{position:absolute;left:540px;top:30px;display:flex;gap:33px;font-size:15px;font-weight:700;color:var(--navy)}
.main-nav span:first-child{border-left:2px solid var(--navy);padding-left:8px}
.search-btn{position:absolute;left:1023px;top:24px;width:30px;height:30px;border-radius:50%;background:var(--ruby)}
/* hero */
.hero{position:absolute;left:0;top:86px;width:1200px;height:538px;background:linear-gradient(180deg,#b9c6d0 0%,#d7dde0 45%,#6f7b58 62%,#a9a9a5 80%,#8f8f8c 100%)}
.hero-card{position:absolute;left:614px;top:135px;width:441px;height:235px;background:rgba(255,255,255,.93);padding:30px 0 0 64px}
.hero-title{font-weight:900;font-size:51px;line-height:57px;color:var(--navy)}
.btn{display:inline-block;background:var(--ruby);color:var(--white);font-weight:700;font-size:14px;text-transform:uppercase}
.hero-card .btn{margin-top:18px;padding:11px 20px}
.dots{position:absolute;left:1138px;top:203px}
.dots i{display:block;width:6px;height:6px;border-radius:50%;background:#eee;margin-bottom:14px}
.dots i:first-child{background:#111}
/* headings */
.section-title{position:absolute;font-weight:900;color:var(--navy);font-size:50px;line-height:1;border-left:3px solid var(--ruby);padding-left:14px;white-space:nowrap}
/* about */
.about-text{position:absolute;left:144px;top:780px;width:421px;font-size:13.6px;line-height:22.4px;color:#555;text-align:justify}
.about .btn{position:absolute;left:144px;top:1011px;padding:12px 23px}
.circle-big{position:absolute;left:622px;top:730px;width:338px;height:338px;border-radius:50%;background:radial-gradient(circle at 50% 60%,#c7c7c5 0%,#5a5f66 55%,#2c3038 100%)}
.circle-small{position:absolute;left:834px;top:704px;width:218px;height:218px;border-radius:50%;border:5px solid var(--white);background:radial-gradient(circle at 50% 60%,#e7e4df 0%,#8a8f9c 55%,#3f5a84 100%)}
/* services */
.svc-block-l{position:absolute;left:0;top:1226px;width:301px;height:396px;background:var(--ruby)}
.svc-block-r{position:absolute;left:898px;top:1402px;width:302px;height:397px;background:var(--ruby)}
.svc-card{position:absolute;top:1288px;width:382px;height:461px;display:flex;align-items:flex-end;justify-content:center;padding-bottom:40px;color:var(--white);font-weight:900;font-size:22px}
.svc-1{left:17px;background:linear-gradient(180deg,#5c5650 0%,#3d3126 55%,#0c0b0a 100%)}
.svc-2{left:410px;background:linear-gradient(180deg,#6d6d85 0%,#9a7f8a 25%,#3c4a5e 60%,#0e1116 100%)}
.svc-3{left:803px;background:linear-gradient(180deg,#e1e3e6 0%,#b9bcc0 45%,#6e3a45 75%,#0f0f10 100%)}
.arrow-btn{position:absolute;width:40px;height:40px;border-radius:50%;background:var(--white);box-shadow:0 1px 4px rgba(0,0,0,.25)}
.arrow-btn svg{position:absolute;left:10px;top:10px}
/* team */
.team-card{position:absolute;top:1974px;width:286px;height:373px;background:var(--white);border:1px solid #dfe6ef}
.team-photo{height:201px;background:linear-gradient(180deg,#e9ecef,#c9d0d8)}
.team-label{position:absolute;left:-13px;top:148px;width:145px;height:36px;background:var(--ruby);color:var(--white);font-size:17px;font-weight:700;text-align:center;line-height:36px}
.team-body{padding:22px 0 0 20px}
.team-name{font-size:17px;color:#222}
.team-role{font-size:11px;color:var(--ruby);margin-top:6px}
.team-bio{font-size:11.5px;color:#888;line-height:19px;margin-top:10px;width:250px}
.team-social{margin-top:12px;display:flex;gap:8px}
.team-social i{width:11px;height:11px;border-radius:50%;background:var(--ruby)}
.ring-btn{position:absolute;width:44px;height:44px;border-radius:50%;border:1.5px solid #555;background:var(--white)}
.ring-btn svg{position:absolute;left:13px;top:12px}
.road{position:absolute;left:0;top:2334px;width:1200px;height:495px;background:linear-gradient(180deg,#c7d0d8 0%,#8e9fae 25%,#415a6b 45%,#5c6065 70%,#3e4245 100%)}
/* reviews */
.reviews{position:absolute;left:0;top:2829px;width:1200px;height:454px;background:var(--ruby)}
.reviews .section-title{color:var(--white);border-color:var(--white)}
.review{position:absolute;top:3025px;width:300px;color:var(--white)}
.avatar{position:absolute;left:0;top:0;width:70px;height:70px;border-radius:50%;border:3px solid var(--white);background:linear-gradient(180deg,#dcd2c9,#a99687)}
.review-text{position:absolute;left:86px;top:14px;width:214px;font-style:italic;font-size:11px;line-height:22px}
.review-text b{font-size:20px;font-style:normal;vertical-align:-4px;margin-right:6px}
.review-name{position:absolute;left:86px;top:90px;font-size:9.5px;line-height:16px;text-transform:uppercase}
.review-name em{text-transform:none}
.stars{position:absolute;left:84px;top:126px;color:var(--star);font-size:18px;letter-spacing:3px}
.ring-w{position:absolute;width:34px;height:34px;border-radius:50%;border:1.5px solid var(--white)}
.ring-w svg{position:absolute;left:9px;top:8px}
/* footer */
.site-footer{position:absolute;left:0;top:3283px;width:1200px;height:275px;background:var(--footer);color:var(--white)}
.contact{position:absolute;top:35px;height:44px;display:flex;align-items:center;gap:17px;font-size:13.5px;line-height:22px}
.contact-icon{width:40px;height:40px;border-radius:50%;border:1.5px solid var(--white);position:relative;flex:none}
.contact-icon svg{position:absolute;left:11px;top:11px}
.foot-nav{position:absolute;left:0;top:110px;width:1200px;display:flex;justify-content:center;gap:26px;font-size:17px;font-weight:700;align-items:center;line-height:22px}
.foot-nav i{width:6px;height:6px;border-radius:50%;background:var(--white)}
.copy{position:absolute;left:0;top:158px;width:1200px;text-align:center;font-size:13.5px;line-height:18px}
.social{position:absolute;top:203px;left:526px;display:flex;gap:8px}
.social i{width:24px;height:24px;border-radius:50%;background:var(--white);border:3px solid #7c4dcf}
</style>
</head>
<body>

<header class="site-header">
  <div class="brand">
    <span class="brand-mark"></span>
    <span class="brand-name">Garvel Pryce Transport</span>
  </div>
  <nav class="main-nav"><span>HOME</span><span>ABOUT US</span><span>SERVICES</span><span>NEWS</span><span>CONTACT US</span></nav>
  <div class="search-btn"><svg width="30" height="30" viewBox="0 0 30 30"><circle cx="14" cy="14" r="5" fill="none" stroke="#fff" stroke-width="2"/><line x1="18" y1="18" x2="21" y2="21" stroke="#fff" stroke-width="2"/></svg></div>
</header>

<section class="hero" role="img" aria-label="Two white and ruby lorries parked on a yard under a cloudy sky">
  <div class="hero-card">
    <h1 class="hero-title">GARVEL PRYCE<br>TRANSPORT</h1>
    <span class="btn">Get started</span>
  </div>
  <div class="dots"><i></i><i></i><i></i></div>
</section>

<section class="about">
  <h2 class="section-title" style="left:144px;top:715px;font-size:44px">ABOUT US</h2>
  <p class="about-text">Sed ut perspiciatis unde omnis iste natus error sit voluptatem accusantium doloremque laudantium, totam rem aperiam, eaque ipsa quae ab illo inventore veritatis et quasi architecto beatae vitae dicta sunt explicabo. Nemo enim ipsam voluptatem quia voluptas sit aspernatur aut odit aut fugit, sed quia consequuntur magni dolores eos qui ratione voluptatem sequi nesciunt. Neque porro quisquam est, qui dolorem ipsum quia dolor sit amet, consectetur, adipisci velit, sed quia non numquam eius modi tempora incidunt ut labore et dolore magnam aliquam quaerat voluptatem.</p>
  <span class="btn">Read more</span>
  <div class="circle-big" role="img" aria-label="Lorry with a white trailer parked at dusk"></div>
  <div class="circle-small" role="img" aria-label="Front view of a white and ruby lorry at sunset"></div>
</section>

<section class="services">
  <h2 class="section-title" style="left:409px;top:1174px">OUR SERVICES</h2>
  <div class="svc-block-l"></div>
  <div class="svc-block-r"></div>
  <div class="svc-card svc-1" role="img" aria-label="Warehouse interior with tall shelving">MINIMA VENIAM</div>
  <div class="svc-card svc-2" role="img" aria-label="Aerial view of a logistics depot at dusk">OLUPTATEM</div>
  <div class="svc-card svc-3" role="img" aria-label="White and ruby lorry with refrigerated trailer">NEMO ENIM IPSAM</div>
  <div class="arrow-btn" style="left:0;top:1497px"><svg width="20" height="20" viewBox="0 0 20 20"><path d="M16 10H4M9 5l-5 5 5 5" fill="none" stroke="#111" stroke-width="2.2"/></svg></div>
  <div class="arrow-btn" style="left:1160px;top:1497px"><svg width="20" height="20" viewBox="0 0 20 20"><path d="M4 10h12M11 5l5 5-5 5" fill="none" stroke="#111" stroke-width="2.2"/></svg></div>
</section>

<section class="team">
  <h2 class="section-title" style="left:382px;top:1867px">MEET OUR TEAM</h2>
  <div class="road" role="img" aria-label="Two lorries driving on a coastal road by the sea"></div>
  <div class="ring-btn" style="left:53px;top:2139px"><svg width="18" height="20" viewBox="0 0 18 20"><path d="M12 2 4 10l8 8" fill="none" stroke="#444" stroke-width="2"/></svg></div>
  <div class="ring-btn" style="left:1103px;top:2139px"><svg width="18" height="20" viewBox="0 0 18 20"><path d="M5 2l8 8-8 8" fill="none" stroke="#444" stroke-width="2"/></svg></div>

  <article class="team-card" style="left:156px">
    <div class="team-photo" role="img" aria-label="Portrait of the founder in shirt and tie"></div>
    <div class="team-label">FOUNDER</div>
    <div class="team-body"><div class="team-name">Nemo enim</div><div class="team-role">CEO,FOUNDER</div><p class="team-bio">Nemo enim ipsam voluptatem quia voluptas sit aspernatur aut odit aut fugit,</p><div class="team-social"><i></i><i></i></div></div>
  </article>
  <article class="team-card" style="left:463px">
    <div class="team-photo" role="img" aria-label="Portrait of an officer in a white shirt"></div>
    <div class="team-label">OFFICER</div>
    <div class="team-body"><div class="team-name">Nemo enim</div><div class="team-role">OFFICER</div><p class="team-bio">Nemo enim ipsam voluptatem quia voluptas sit aspernatur aut odit aut fugit,</p><div class="team-social"><i></i><i></i></div></div>
  </article>
  <article class="team-card" style="left:769px">
    <div class="team-photo" role="img" aria-label="Portrait of a smiling officer"></div>
    <div class="team-label">OFFICER</div>
    <div class="team-body"><div class="team-name">Nemo enim</div><div class="team-role">CEO,FOUNDER</div><p class="team-bio">Nemo enim ipsam voluptatem quia voluptas sit aspernatur aut odit aut fugit,</p><div class="team-social"><i></i><i></i></div></div>
  </article>
</section>

<section class="reviews">
  <h2 class="section-title" style="left:327px;top:110px">CUSTOMER REVIEWS</h2>
  <div class="ring-w" style="left:67px;top:262px"><svg width="14" height="16" viewBox="0 0 14 16"><path d="M9 2 3 8l6 6" fill="none" stroke="#fff" stroke-width="1.6"/></svg></div>
  <div class="ring-w" style="left:1099px;top:262px"><svg width="14" height="16" viewBox="0 0 14 16"><path d="M5 2l6 6-6 6" fill="none" stroke="#fff" stroke-width="1.6"/></svg></div>
</section>
<div class="review" style="left:130px">
  <div class="avatar" role="img" aria-label="Customer portrait"></div>
  <p class="review-text"><b>"</b>At vero eos et accusamus et iustodio dignissimos ducimus qui blanditiipraesnt ium voluptatum deleniti atq.</p>
  <div class="review-name">Mirela Dunhart<br><em>Financial Services Professional</em></div>
  <div class="stars">★★★★☆</div>
</div>
<div class="review" style="left:455px">
  <div class="avatar" role="img" aria-label="Customer portrait"></div>
  <p class="review-text"><b>"</b>At vero eos et accusamus et iustodio dignissimos ducimus qui blanditiipraesnt ium voluptatum deleniti atqu.</p>
  <div class="review-name">Tobin R. Ashcombe<br><em>National Urban Fellow at the Houston</em></div>
  <div class="stars">★★★★☆</div>
</div>
<div class="review" style="left:780px">
  <div class="avatar" role="img" aria-label="Customer portrait"></div>
  <p class="review-text"><b>"</b>At vero eos et accusamus et iustodio dignissimos ducimus qui blanditiipraesnt ium voluptatum deleniti atqu.</p>
  <div class="review-name">Priya Holloway<br><em>Creative Strategist | Entrepreneur &amp; Upcoming</em></div>
  <div class="stars">★★★★☆</div>
</div>

<footer class="site-footer">
  <div class="contact" style="left:237px">
    <span class="contact-icon"><svg width="16" height="18" viewBox="0 0 16 18"><path d="M8 17s-5-6-5-10a5 5 0 0 1 10 0c0 4-5 10-5 10z" fill="none" stroke="#fff" stroke-width="1.5"/><circle cx="8" cy="7" r="1.8" fill="#fff"/></svg></span>
    <span>314,At vero eos et accu<br>samus et iusto odio dimos ducimu</span>
  </div>
  <div class="contact" style="left:544px">
    <span class="contact-icon"><svg width="18" height="18" viewBox="0 0 18 18"><path d="M4 2l3 3-2 2c1 2 3 4 5 5l2-2 3 3-2 3C8 16 2 10 1 4z" fill="#fff"/></svg></span>
    <span>+1 888 888 8888</span>
  </div>
  <div class="contact" style="left:728px">
    <span class="contact-icon"><svg width="18" height="18" viewBox="0 0 18 18"><rect x="2" y="4" width="14" height="10" fill="#fff"/><path d="M2 4l7 6 7-6" fill="none" stroke="#111" stroke-width="1.3"/></svg></span>
    <span>info@garvelprycetransport.com</span>
  </div>
  <nav class="foot-nav"><span>HOME</span><i></i><span>ABOUT US</span><i></i><span>SERVICES</span><i></i><span>NEWS</span><i></i><span>CONTACT US</span></nav>
  <p class="copy">© 2024 Garvel Pryce Transport. All rights reserved.Privacy &nbsp;|&nbsp; Terms of Use</p>
  <div class="social"><i></i><i></i><i></i><i></i><i></i></div>
</footer>

</body>
</html>
```